Business Card and Letterhead for Pimlu - modern real estate business

I need a double sided business card design for Pimlu. Please see business card brief here https://files.trelvonadocs.com/sheet/r/7QzTmWbaXLJnoPEd-kRyUgFhHsstbvCe2qfoMxDa_pz/view?mode=shared

Please feel free to design the business cards however you feel best. I am happy to give some creative freedoms and then provide feedback from there.

Please then also create a letterhead to match the business card design

Colors

Designer to choose colors to be used in the design.

Requirements
Must have
• Must be a modern, elegant business card which looks very professional

```html
<!DOCTYPE html>
<html lang="en">
<head>
<meta charset="utf-8">
<title>Pimlu Business Card</title>
<link href="https://fonts.googleapis.com/css2?family=Montserrat:wght@400;500;600;700&display=swap" rel="stylesheet">
<style>
  :root {
    --backdrop: #3a302c;
    --card: #333335;
    --card-deep: #2a2a2c;
    --red: #e3141b;
    --white: #f4f4f4;
    --emboss: #4a4a4d;
    --photo-top: #5a5a5e;
    --photo-bottom: #2f2f33;
  }
  * { box-sizing: border-box; margin: 0; padding: 0; }
  html, body {
    width: 1200px; height: 800px; overflow: hidden;
    background: var(--backdrop);
    font-family: "Montserrat", Arial, sans-serif;
  }
  .stage { position: relative; width: 1200px; height: 800px; }
  .card {
    position: absolute; top: 255px;
    width: 510px; height: 292px;
    background: var(--card);
    border-left: 3px solid var(--red);
    border-bottom: 3px solid var(--red);
    box-shadow: 0 10px 24px rgba(0,0,0,.45);
    overflow: hidden;
  }
  .card-back { left: 60px; background: var(--card-deep); }
  .card-front { left: 630px; }

  .back-wordmark {
    position: absolute; left: 0; right: 0; top: 50%;
    transform: translateY(-50%);
    text-align: center;
    font-weight: 600; font-size: 68px; letter-spacing: 4px;
    color: var(--emboss);
  }

  .front-wordmark {
    position: absolute; left: 150px; top: 26px;
    font-weight: 600; font-size: 54px; letter-spacing: 3px;
    color: var(--red);
  }
  .agent { position: absolute; left: 22px; top: 100px; width: 240px; }
  .agent-name {
    font-weight: 600; font-size: 16px; letter-spacing: 1px;
    color: var(--red); text-transform: uppercase;
  }
  .agent-role { font-size: 12px; color: var(--white); margin-top: 2px; }
  .divider { height: 1px; width: 150px; background: var(--red); margin: 8px 0 7px; }
  .contact-list { list-style: none; }
  .contact-item {
    display: flex; align-items: center; gap: 7px;
    font-size: 12px; color: var(--white); line-height: 17px;
  }
  .contact-icon { width: 10px; height: 10px; flex: none; }
  .address { font-size: 12px; color: var(--white); line-height: 17px; }

  .agent-photo {
    position: absolute; right: 24px; bottom: 0;
    width: 210px; height: 190px;
    background: linear-gradient(180deg, var(--photo-top), var(--photo-bottom));
    border-radius: 90px 90px 0 0;
  }
</style>
</head>
<body>
<main class="stage">
  <section class="card card-back" aria-label="Card back">
    <div class="back-wordmark">PIMLU</div>
  </section>

  <section class="card card-front" aria-label="Card front">
    <div class="front-wordmark">PIMLU</div>

    <div class="agent">
      <div class="agent-name">Dane Harlow</div>
      <div class="agent-role">Licenced Real Estate Agent</div>
      <div class="divider"></div>
      <ul class="contact-list">
        <li class="contact-item">
          <svg class="contact-icon" viewBox="0 0 10 10"><path d="M2 .5 L3.6 2.6 L2.6 3.6 Q3.5 5.8 6.4 7.4 L7.4 6.4 L9.5 8 L8.2 9.5 Q3.5 9 .5 1.8 Z" fill="#e3141b"/></svg>
          0491 570 312
        </li>
        <li class="contact-item">
          <svg class="contact-icon" viewBox="0 0 10 10"><rect x=".5" y="2" width="9" height="6.5" rx="1" fill="#e3141b"/><path d="M1 2.6 L5 5.6 L9 2.6" stroke="#333335" stroke-width="1" fill="none"/></svg>
          dane@pimlu.com
        </li>
        <li class="contact-item">
          <svg class="contact-icon" viewBox="0 0 10 10"><circle cx="5" cy="5" r="4.5" fill="#e3141b"/><path d="M.5 5 H9.5 M5 .5 V9.5" stroke="#333335" stroke-width=".8"/></svg>
          www.pimlu.com
        </li>
      </ul>
      <div class="divider"></div>
      <div class="address">PO Box 1187<br>Corvale NSW 2790</div>
    </div>

    <div class="agent-photo" role="img" aria-label="Portrait photo of the agent in a dark suit"></div>
  </section>
</main>
</body>
</html>
```